tinyTally Resource Book - 10 maths tasks to do outside

I need a 22 (11 pages back to back) page A6 sized book produced to standard for submission to professional printer. Needs to be as .pdf file showing guide lines and allowances for colour bleed. I have text already written and submitted as attachment in a Word file with margins set to A6 size. The theme of the materials is "Nature Play" so using lots of pictures from nature (Australia preferably) and showing lots of patterns in nature (rocks, leaves, flower petals etc). Some of the tasks refer to specific activities, such as "shadows" and "floating" so would be great to illustrate appropriately. The big emphasis is on learning outside the classroom, getting kids to engage actively with nature. I would like to see the pages as full colour - so not white background. The book itself will be spiral bound along the top edge so a margin of at least 1cm will be required at the top of each page (or the bottom of even numbered pages). Book will be printed on plastic laminated matte paper for outdoor use. Font size needs to be big enough to read. Fonts sizes, alignments and page numbers are all different at the moment and need to be standardised. One photo is included in a page as a sample if you can use it, otherwise disregard. Logo for Wattlebrook Numeracy Guild is also included to have as part of the acknowledgements at the back of the book.

Target Market(s)

Book is for early childhood and preschool teachers.

Industry/Entity Type

Education

Font styles to use
Sans Serif

Requirements
Must have
• Colour and appeal.
Nice to have
• Use of natural colours instead of bright catchy colours but that is your call.
Should not have
• American spelling

```html
<!DOCTYPE html>
<html lang="en-AU">
<head>
<meta charset="utf-8">
<title>tinyTally – Same Same Different</title>
<link rel="stylesheet" href="https://fonts.googleapis.com/css2?family=Jost:wght@500;600;800;900&display=swap">
<style>
  :root {
    --ink-blue: #2b3593;
    --ink-dark: #1c1a17;
    --bullet-red: #d3202a;
    --halo: #fffaf0;
    --sand-light: #f6e9c4;
    --sand-mid: #e4cd94;
    --sand-deep: #c9a86a;
    --stone-shadow: #a98d60;
  }
  * { margin: 0; padding: 0; box-sizing: border-box; }
  html, body {
    width: 848px; height: 1200px; overflow: hidden;
    background: var(--sand-mid);
  }
  .page {
    position: relative; width: 848px; height: 1200px; overflow: hidden;
    font-family: "Jost", "Century Gothic", sans-serif;
    color: var(--ink-dark);
  }
  .nature-photo {
    position: absolute; inset: 0;
    background:
      radial-gradient(ellipse 260px 420px at 640px 880px, rgba(169,141,96,0.55), rgba(169,141,96,0) 70%),
      radial-gradient(ellipse 520px 360px at 360px 260px, rgba(255,250,230,0.7), rgba(255,250,230,0) 75%),
      linear-gradient(180deg, var(--sand-light) 0%, var(--sand-mid) 55%, var(--sand-deep) 100%);
  }
  .content { position: absolute; left: 58px; top: 72px; right: 40px; }
  .task-title, .section-title {
    color: var(--ink-blue);
    font-weight: 900;
    line-height: 1;
    text-shadow:
      2px 2px 0 var(--halo), -2px 2px 0 var(--halo),
      2px -2px 0 var(--halo), -2px -2px 0 var(--halo),
      0 3px 0 var(--halo), 3px 0 0 var(--halo);
  }
  .task-title { font-size: 56px; letter-spacing: 0.5px; }
  .section-title { font-size: 45px; margin-top: 36px; }
  .points { list-style: none; margin-left: 80px; margin-top: 12px; }
  .points li {
    position: relative; padding-left: 28px;
    font-size: 30px; font-weight: 500; line-height: 41px;
  }
  .points li::before {
    content: ""; position: absolute; left: 0; top: 13px;
    width: 14px; height: 14px; background: var(--bullet-red);
    transform: rotate(45deg);
  }
  .prompt { font-size: 30px; font-weight: 500; line-height: 42px; margin-top: 10px; }
</style>
</head>
<body>
  <main class="page">
    <div class="nature-photo" role="img" aria-label="Photograph of a small stack of smooth river stones balanced on sand, casting a soft shadow"></div>
    <section class="content">
      <h1 class="task-title">3. Same Same Different</h1>
      <ul class="points">
        <li>Get 3 objects</li>
        <li>Ask partner to say which two are the same and which one is different</li>
        <li>Discuss attributes that are the same and different</li>
        <li>Swap roles with partner</li>
      </ul>

      <h2 class="section-title">Prompting questions</h2>
      <p class="prompt">Can you keep the same objects but have a new “different” object?</p>

      <h2 class="section-title">Variations</h2>
      <ul class="points">
        <li>Same Same Same</li>
        <li>Different Different Different</li>
      </ul>

      <h2 class="section-title">Big Ideas</h2>
      <ul class="points">
        <li>Same and different</li>
        <li>Justifying an idea</li>
        <li>Finding relationships</li>
        <li>Compare and contrast</li>
      </ul>
    </section>
  </main>
</body>
</html>
```